Cafe - A FRAME Design

Need to create an A frame for my café.
Logo available
Word document - has basic information we think would be good.

Name: Wuzzop Café

Notes from the A-frame printers.
File Requirements
• PDF without trim, crop or registration marks
• All files to be CMYK, not RGB
• All fonts converted to outlines (paths/curves)
• Embed all images and elements
• Files to be 100% scale unless otherwise specified
• 10mm Bleed
Resolution
• Bitmap images no less than 130 DPI at full size
Pantone Colours
• If required Pantone colours must be supplied

Target Market(s)

Mainly Students - University cafe

Requirements
Must have
• Cafe name: Wuzzop
Nice to have
• Might be nice to have background - that orange color same as logo - just an idea

Word document - has basic idea regarding text that should be included

```html
<!DOCTYPE html>
<html lang="en">
<head>
<meta charset="utf-8">
<title>Wuzzop Café – A-Frame Poster</title>
<link rel="stylesheet" href="https://fonts.googleapis.com/css2?family=Montserrat:wght@500;600;700;800;900&display=swap">
<style>
  :root {
    --orange: #f26522;
    --orange-deep: #e2561a;
    --ink: #3b3b3b;
    --rule: #b9b9b9;
    --paper: #ffffff;
    --photo-light: #e9e4de;
    --photo-mid: #b8aea3;
    --photo-dark: #6f655c;
  }
  * { box-sizing: border-box; margin: 0; padding: 0; }
  html, body { width: 800px; height: 1200px; overflow: hidden; background: var(--paper); }
  body { font-family: "Montserrat", Arial, sans-serif; color: var(--ink); }

  .poster { position: relative; width: 800px; height: 1200px; display: flex; flex-direction: column; align-items: center; }

  .brand { margin-top: 58px; display: flex; align-items: center; gap: 16px; }
  .brand-mark { width: 44px; height: 44px; background: var(--orange); border-radius: 6px; }
  .brand-name { font-size: 54px; font-weight: 700; color: var(--ink); letter-spacing: 0.5px; line-height: 1; }

  .headline { margin-top: 44px; width: 640px; text-align: center; }
  .headline-frame { border: 3px solid var(--rule); padding: 18px 10px 14px; }
  .headline-lead { font-size: 40px; font-weight: 800; line-height: 1.15; text-transform: uppercase; color: var(--ink); }
  .headline-lead .accent { color: var(--orange); }
  .headline-main { margin-top: 10px; font-size: 78px; font-weight: 900; color: var(--orange); text-transform: uppercase; line-height: 1.05; letter-spacing: 1px; }

  .offer-list { margin-top: 34px; width: 600px; display: grid; grid-template-columns: 1fr 1fr; row-gap: 18px; column-gap: 30px; list-style: none; }
  .offer-item { display: flex; align-items: center; gap: 14px; font-size: 22px; font-weight: 600; color: var(--ink); }
  .offer-item.wide { grid-column: 1 / -1; }
  .offer-icon { flex: none; width: 36px; height: 36px; background: var(--orange); border-radius: 50%; display: flex; align-items: center; justify-content: center; }

  .cafe-photo { margin-top: 36px; width: 800px; flex: 1; background: linear-gradient(160deg, var(--photo-light) 0%, var(--photo-mid) 55%, var(--photo-dark) 100%); }

  .location-band { width: 800px; height: 130px; background: var(--orange); display: flex; align-items: center; justify-content: center; }
  .location-text { color: var(--paper); font-size: 52px; font-weight: 800; letter-spacing: 0.5px; }
</style>
</head>
<body>
<main class="poster">
  <header class="brand">
    <span class="brand-mark"></span>
    <span class="brand-name">Wuzzop</span>
  </header>

  <section class="headline">
    <div class="headline-frame">
      <p class="headline-lead">Your <span class="accent">Environmentally</span><br>&amp; Sustainability</p>
    </div>
    <h1 class="headline-main">Focused Café</h1>
  </section>

  <ul class="offer-list">
    <li class="offer-item">
      <span class="offer-icon"><svg width="20" height="20" viewBox="0 0 20 20"><path d="M4 10.5l4 4 8-9" fill="none" stroke="#fff" stroke-width="2.6" stroke-linecap="round" stroke-linejoin="round"/></svg></span>
      Speciality Coffee
    </li>
    <li class="offer-item">
      <span class="offer-icon"><svg width="20" height="20" viewBox="0 0 20 20"><path d="M4 10.5l4 4 8-9" fill="none" stroke="#fff" stroke-width="2.6" stroke-linecap="round" stroke-linejoin="round"/></svg></span>
      Pastries &amp; Drinks
    </li>
    <li class="offer-item">
      <span class="offer-icon"><svg width="20" height="20" viewBox="0 0 20 20"><path d="M4 10.5l4 4 8-9" fill="none" stroke="#fff" stroke-width="2.6" stroke-linecap="round" stroke-linejoin="round"/></svg></span>
      Fresh Food
    </li>
    <li class="offer-item">
      <span class="offer-icon"><svg width="20" height="20" viewBox="0 0 20 20"><path d="M4 10.5l4 4 8-9" fill="none" stroke="#fff" stroke-width="2.6" stroke-linecap="round" stroke-linejoin="round"/></svg></span>
      Catering Available
    </li>
    <li class="offer-item wide">
      <span class="offer-icon"><svg width="20" height="20" viewBox="0 0 20 20"><path d="M4 10.5l4 4 8-9" fill="none" stroke="#fff" stroke-width="2.6" stroke-linecap="round" stroke-linejoin="round"/></svg></span>
      Vegan &amp; GF options available
    </li>
  </ul>

  <div class="cafe-photo" role="img" aria-label="Photo of the café interior with customers at the counter and tables"></div>

  <footer class="location-band">
    <p class="location-text">Located @ Building 202</p>
  </footer>
</main>
</body>
</html>
```